Biz Cards to match new logo

I'm looking for a business card layout to go with my new logo. I'd like to have one side in colour (purple, with the logo in white) and the other side to be white with the purple logo and contact info in black font: name, address (2 lines), phone, email, fax, website. The logo includes the company name so it doesn't need to be repeated in the text. The font should be legibile to the semi-blind. (I hate small fonts on business cards).

Industry/Entity Type

Business

```html
<!DOCTYPE html>
<html lang="en">
<head>
<meta charset="utf-8">
<title>Vireo Analytics – Business Cards</title>
<link rel="stylesheet" href="https://fonts.googleapis.com/css2?family=Open+Sans:wght@400;600&display=swap">
<style>
  :root {
    --backdrop: #d9d9dc;
    --purple: #623d8f;
    --purple-deep: #57347f;
    --card-white: #f4f4f4;
    --ink: #1c1c1c;
    --logo-white: #ffffff;
  }
  * { margin: 0; padding: 0; box-sizing: border-box; }
  html, body {
    width: 1200px;
    height: 1200px;
    overflow: hidden;
    background: var(--backdrop);
    font-family: "Open Sans", Arial, sans-serif;
  }
  .sheet {
    width: 1200px;
    height: 1200px;
    display: flex;
    flex-direction: column;
    align-items: center;
    justify-content: center;
    gap: 52px;
  }
  .card {
    position: relative;
    width: 900px;
    height: 514px;
    border-radius: 6px;
    overflow: hidden;
    box-shadow: 0 10px 28px rgba(0, 0, 0, 0.22);
  }

  /* Front side */
  .card-front {
    background: linear-gradient(135deg, var(--purple) 0%, var(--purple-deep) 100%);
    display: flex;
    align-items: center;
    justify-content: center;
  }
  .wordmark {
    display: flex;
    align-items: center;
    gap: 18px;
    font-weight: 600;
    letter-spacing: 0.08em;
    text-transform: uppercase;
  }
  .wordmark-square {
    display: block;
    background: currentColor;
  }
  .card-front .wordmark {
    color: var(--logo-white);
    font-size: 54px;
    margin-left: 120px;
  }
  .card-front .wordmark-square { width: 44px; height: 44px; }

  /* Back side */
  .card-back { background: var(--card-white); }
  .back-band {
    position: absolute;
    top: 0; left: 0; right: 0;
    height: 178px;
    background: var(--purple);
    display: flex;
    align-items: center;
    padding-left: 78px;
  }
  .card-back .wordmark {
    color: var(--logo-white);
    font-size: 30px;
    gap: 12px;
  }
  .card-back .wordmark-square { width: 24px; height: 24px; }
  .holder-name {
    position: absolute;
    top: 200px;
    left: 118px;
    font-size: 32px;
    font-weight: 600;
    color: var(--purple);
  }
  .contact-block {
    position: absolute;
    top: 262px;
    left: 78px;
    display: flex;
    gap: 22px;
  }
  .contact-rule {
    width: 9px;
    background: var(--purple);
    border-radius: 2px;
  }
  .contact-list {
    list-style: none;
    font-size: 26px;
    line-height: 1.3;
    color: var(--ink);
  }
</style>
</head>
<body>
  <main class="sheet">
    <section class="card card-front" aria-label="Business card front">
      <div class="wordmark">
        <span class="wordmark-square" aria-hidden="true"></span>
        <span class="wordmark-name">Vireo Analytics</span>
      </div>
    </section>

    <section class="card card-back" aria-label="Business card back">
      <header class="back-band">
        <div class="wordmark">
          <span class="wordmark-square" aria-hidden="true"></span>
          <span class="wordmark-name">Vireo Analytics</span>
        </div>
      </header>
      <p class="holder-name">Name</p>
      <div class="contact-block">
        <span class="contact-rule" aria-hidden="true"></span>
        <ul class="contact-list">
          <li>Address line 1</li>
          <li>Address line 2</li>
          <li>Phone</li>
          <li>Email</li>
          <li>Fax</li>
          <li>website</li>
        </ul>
      </div>
    </section>
  </main>
</body>
</html>
```